Harborline Auto LLC

Car Dealer Customer Service
Address: 2874 Cresthaven Road, Shelbyville, TN 37162
web: www.harborlineautoxq.net
email: harborlineautoxq@mailnest.example
Phone: (931) 555-0148
Phone: (629) 555-0173

```html
<!DOCTYPE html>
<html lang="en">
<head>
<meta charset="utf-8">
<title>Harborline Auto LLC – Business Card</title>
<link rel="stylesheet" href="https://fonts.googleapis.com/css2?family=Montserrat:wght@500;800&family=Nunito+Sans:wght@400&display=swap">
<style>
  :root {
    --backdrop: #3f4043;
    --brand-blue: #1f7cad;
    --accent-blue: #2a93cf;
    --paper: #ffffff;
    --ink: #1d1d1f;
    --shadow: rgba(0,0,0,0.45);
  }
  * { margin: 0; padding: 0; box-sizing: border-box; }
  html, body { width: 1200px; height: 887px; overflow: hidden; }
  body {
    background: var(--backdrop);
    position: relative;
    font-family: "Nunito Sans", Arial, sans-serif;
  }
  .card {
    position: absolute;
    left: 290px;
    width: 620px;
    height: 354px;
    border-radius: 28px;
    overflow: hidden;
    box-shadow: 0 14px 30px var(--shadow);
  }
  .card-front { top: 52px; background: var(--brand-blue); }
  .card-back { top: 478px; background: var(--paper); }

  .brand {
    display: flex;
    align-items: center;
    gap: 18px;
    font-family: "Montserrat", Arial, sans-serif;
    font-weight: 800;
    text-transform: uppercase;
    letter-spacing: 1px;
  }
  .brand-dot { border-radius: 50%; flex: none; }

  .card-front .brand {
    position: absolute; inset: 0;
    justify-content: center;
    color: var(--paper);
    font-size: 40px;
  }
  .card-front .brand-dot { width: 64px; height: 64px; border: 8px solid var(--paper); }

  .card-back .brand {
    position: absolute; left: 48px; top: 44px;
    color: var(--brand-blue);
    font-size: 28px;
  }
  .card-back .brand-dot { width: 46px; height: 46px; background: var(--accent-blue); }

  .side-bar {
    position: absolute; right: 0; top: 92px;
    width: 16px; height: 64px;
    background: var(--accent-blue);
  }
  .address {
    position: absolute; right: 40px; top: 88px;
    text-align: right;
    font-style: normal;
    font-family: "Montserrat", Arial, sans-serif;
    font-weight: 500;
    font-size: 16px;
    line-height: 1.4;
    color: var(--ink);
  }
  .contact-list {
    position: absolute; left: 48px; bottom: 40px;
    list-style: none;
    font-family: "Montserrat", Arial, sans-serif;
    font-weight: 500;
    font-size: 17px;
    color: var(--ink);
  }
  .contact-list li {
    display: flex; align-items: center; gap: 12px;
    line-height: 1.55;
  }
  .contact-icon { width: 16px; height: 16px; flex: none; }
</style>
</head>
<body>
  <section class="card card-front" aria-label="Card front">
    <div class="brand"><span class="brand-dot"></span><span class="brand-name">Harborline Auto</span></div>
  </section>

  <section class="card card-back" aria-label="Card back">
    <div class="brand"><span class="brand-dot"></span><span class="brand-name">Harborline Auto</span></div>
    <span class="side-bar"></span>
    <address class="address">
      Car Dealer Customer Service<br>
      2874 Cresthaven Road<br>
      Shelbyville, TN 37162
    </address>
    <ul class="contact-list">
      <li>
        <svg class="contact-icon" viewBox="0 0 16 16"><path fill="#2a93cf" d="M3 1l3 3-1.5 2a9 9 0 0 0 5.5 5.5L12 10l3 3-2 2C7 15 1 9 1 3z"/></svg>
        (931) 555-0148
      </li>
      <li>
        <svg class="contact-icon" viewBox="0 0 16 16"><path fill="#2a93cf" d="M1 6c0-2 3-3 7-3s7 1 7 3v1h-3V5.5H4V7H1zM3 8h10l1 6H2z"/></svg>
        (629) 555-0173
      </li>
      <li>
        <svg class="contact-icon" viewBox="0 0 16 16"><rect x="1" y="3" width="14" height="10" rx="1" fill="#2a93cf"/><path d="M1.5 4l6.5 5 6.5-5" fill="none" stroke="#fff" stroke-width="1.2"/></svg>
        harborlineautoxq@mailnest.example
      </li>
      <li>
        <svg class="contact-icon" viewBox="0 0 16 16"><circle cx="8" cy="8" r="7" fill="#2a93cf"/><path d="M1 8h14M8 1c-3 3-3 11 0 14M8 1c3 3 3 11 0 14" fill="none" stroke="#fff" stroke-width="1"/></svg>
        www.harborlineautoxq.net
      </li>
    </ul>
  </section>
</body>
</html>
```